Kelbrook Plumbing flyer

I want to incorporate our logo design into a new flyer promoting the business and advertising products that we install.
We install hot water systems, Air-conditioning systems and central heating systems. Along with other aspects of plumbing such as gasfitting, roofing, sanitary and drainage
I would like the background to be the same as our business cards with the water effect and colours.

Requirements
Must have
• Logo
24/7 Emergency call out
Aspects of plumbing we do
- Hot water systems
- Central Heating
- Solar hot water systems/ heat pump systems
- Gasfitting
- Drainage
- Roofing
- Air-Conditioning
Nice to have
• Pictures of hot water systems and air-conditioning system
$30 off voucher when producing this flyer (limit 1 per house hold)

```html
<!DOCTYPE html>
<html lang="en">
<head>
<meta charset="utf-8">
<title>Kelbrook Plumbing Flyer</title>
<link rel="stylesheet" href="https://fonts.googleapis.com/css2?family=Montserrat:wght@400;500;600;700;800;900&family=Nunito:wght@800;900&display=swap">
<style>
:root{
  --page:#eceeef;
  --navy:#0b2a50;
  --navy-deep:#07203f;
  --blue:#0a7fd0;
  --sky:#19a4ea;
  --charcoal:#35383d;
  --red:#b11e24;
  --white:#ffffff;
}
*{box-sizing:border-box;margin:0;padding:0}
html,body{width:1200px;height:900px;overflow:hidden;background:var(--page)}
body{position:relative;font-family:"Montserrat",sans-serif}
.flyer{position:absolute;top:82px;width:520px;height:735px;overflow:hidden;background:var(--navy);box-shadow:0 10px 30px rgba(0,0,0,.18)}
.flyer--services{left:50px}
.flyer--promise{left:630px}
.flyer__art{position:absolute;inset:0;width:520px;height:735px}
.brand{position:absolute;left:30px;top:44px;display:flex;align-items:center;gap:14px}
.brand__dot{width:44px;height:44px;border-radius:50%;background:var(--sky)}
.brand__name{font-family:"Montserrat",sans-serif;font-weight:800;font-size:30px;line-height:1.02;color:var(--sky);text-transform:uppercase;letter-spacing:.5px}
.headline{position:absolute;left:22px;top:262px;font-family:"Nunito",sans-serif;line-height:1}
.headline__lead,.headline__tail{display:block;color:var(--sky);font-weight:900;font-size:22px}
.headline__main{display:block;color:var(--white);font-weight:900;font-size:36px;letter-spacing:.5px;margin:2px 0}
.provide{position:absolute;left:22px;top:352px;font-family:"Nunito",sans-serif;font-weight:900;font-size:16px;color:var(--sky)}
.ticks{position:absolute;left:22px;list-style:none;color:var(--white)}
.ticks li{display:flex;align-items:center;gap:9px}
.tick{width:13px;height:13px;flex:none}
.ticks--services{top:402px}
.ticks--services li{font-size:13.5px;font-weight:500;text-transform:uppercase;letter-spacing:.3px;height:25px}
.ticks--promise{top:352px}
.ticks--promise li{font-size:12.5px;font-weight:500;height:24px}
.call{position:absolute;left:18px;font-weight:900;font-size:23px;color:var(--white);letter-spacing:.5px}
.flyer--services .call{top:654px}
.flyer--promise .call{top:480px;font-size:22px}
.contact{position:absolute;left:22px;font-size:11.5px;font-weight:500;color:var(--white)}
.flyer--services .contact{top:701px}
.flyer--promise .contact{top:700px}
.licence{position:absolute;right:26px;text-align:center;color:var(--white)}
.flyer--services .licence{top:690px}
.flyer--promise .licence{top:688px}
.licence__label{display:block;font-size:9px;font-weight:500}
.licence__number{display:block;font-size:21px;font-weight:600;letter-spacing:1px}
.badge__time{position:absolute;left:388px;top:425px;width:110px;text-align:center;color:var(--white);font-weight:700;line-height:1}
.badge__hours{display:block;font-size:30px}
.badge__label{display:block;font-size:14px;margin-top:3px;letter-spacing:.5px}
</style>
</head>
<body>

<article class="flyer flyer--services">
  <svg class="flyer__art" viewBox="0 0 520 735">
    <defs>
      <radialGradient id="waterTextureA" cx="0.7" cy="0.3" r="0.9">
        <stop offset="0" stop-color="#4a4e54"/><stop offset="1" stop-color="#2b2e33"/>
      </radialGradient>
      <linearGradient id="acPhoto" x1="0" y1="0" x2="1" y2="1">
        <stop offset="0" stop-color="#b8906f"/><stop offset=".55" stop-color="#6a7a90"/><stop offset="1" stop-color="#e4e0da"/>
      </linearGradient>
      <linearGradient id="sinkPhoto" x1="0" y1="0" x2="1" y2="1">
        <stop offset="0" stop-color="#e9ecef"/><stop offset=".5" stop-color="#b24a40"/><stop offset="1" stop-color="#6b6f76"/>
      </linearGradient>
    </defs>
    <rect width="520" height="340" fill="url(#waterTextureA)" role="img" aria-label="Dark background covered in water droplets"/>
    <path d="M0 232 C130 200 250 210 330 290 C400 360 470 380 520 350 L520 735 L0 735 Z" fill="var(--navy)"/>
    <path d="M0 214 C130 182 250 192 330 272 C400 342 470 362 520 332" fill="none" stroke="var(--blue)" stroke-width="16"/>
    <path d="M0 228 C130 196 250 206 330 286 C400 356 470 376 520 346" fill="none" stroke="var(--sky)" stroke-width="6"/>
    <path d="M300 378 L520 378 L520 500 C450 525 370 485 300 505 Z" fill="url(#acPhoto)" role="img" aria-label="Photo of a technician servicing an air-conditioning unit with pressure gauges"/>
    <path d="M300 540 C370 518 450 558 520 535 L520 642 L290 642 Z" fill="url(#sinkPhoto)" role="img" aria-label="Photo of a plumber fixing pipes under a sink with a red wrench"/>
    <path d="M0 642 L400 642 L380 684 L0 684 Z" fill="var(--sky)"/>
    <path d="M380 684 L400 642 L520 642 L520 735 L0 735 L0 684 Z" fill="var(--navy-deep)"/>
  </svg>
  <div class="brand"><span class="brand__dot"></span><span class="brand__name">Kelbrook<br>Plumbing</span></div>
  <h1 class="headline"><span class="headline__lead">Need a Premium</span><span class="headline__main">PLUMBING</span><span class="headline__tail">Service?</span></h1>
  <p class="provide">We Provide:</p>
  <ul class="ticks ticks--services">
    <li><svg class="tick" viewBox="0 0 14 14"><circle cx="7" cy="7" r="7" fill="#fff"/><path d="M3.8 7.2l2.2 2.2 4.2-4.4" fill="none" stroke="#0b2a50" stroke-width="1.8"/></svg>Plumbing &amp; Gasfitting</li>
    <li><svg class="tick" viewBox="0 0 14 14"><circle cx="7" cy="7" r="7" fill="#fff"/><path d="M3.8 7.2l2.2 2.2 4.2-4.4" fill="none" stroke="#0b2a50" stroke-width="1.8"/></svg>Air-Conditioning</li>
    <li><svg class="tick" viewBox="0 0 14 14"><circle cx="7" cy="7" r="7" fill="#fff"/><path d="M3.8 7.2l2.2 2.2 4.2-4.4" fill="none" stroke="#0b2a50" stroke-width="1.8"/></svg>Blocked Drains</li>
    <li><svg class="tick" viewBox="0 0 14 14"><circle cx="7" cy="7" r="7" fill="#fff"/><path d="M3.8 7.2l2.2 2.2 4.2-4.4" fill="none" stroke="#0b2a50" stroke-width="1.8"/></svg>Hot Water Systems</li>
    <li><svg class="tick" viewBox="0 0 14 14"><circle cx="7" cy="7" r="7" fill="#fff"/><path d="M3.8 7.2l2.2 2.2 4.2-4.4" fill="none" stroke="#0b2a50" stroke-width="1.8"/></svg>Central Heating</li>
    <li><svg class="tick" viewBox="0 0 14 14"><circle cx="7" cy="7" r="7" fill="#fff"/><path d="M3.8 7.2l2.2 2.2 4.2-4.4" fill="none" stroke="#0b2a50" stroke-width="1.8"/></svg>Roofing</li>
    <li><svg class="tick" viewBox="0 0 14 14"><circle cx="7" cy="7" r="7" fill="#fff"/><path d="M3.8 7.2l2.2 2.2 4.2-4.4" fill="none" stroke="#0b2a50" stroke-width="1.8"/></svg>Sanitary and Drainage</li>
    <li><svg class="tick" viewBox="0 0 14 14"><circle cx="7" cy="7" r="7" fill="#fff"/><path d="M3.8 7.2l2.2 2.2 4.2-4.4" fill="none" stroke="#0b2a50" stroke-width="1.8"/></svg>Solar Hot Water</li>
  </ul>
  <p class="call">CALL US : 0400 555 218</p>
  <p class="contact">www.kelbrookplumbing.com | info@kelbrookplumbing.com</p>
  <p class="licence"><span class="licence__label">Licence Number</span><span class="licence__number">204817</span></p>
</article>

<article class="flyer flyer--promise">
  <svg class="flyer__art" viewBox="0 0 520 735">
    <defs>
      <radialGradient id="waterTextureB" cx="0.7" cy="0.3" r="0.9">
        <stop offset="0" stop-color="#4a4e54"/><stop offset="1" stop-color="#2b2e33"/>
      </radialGradient>
      <path id="badgeArc" d="M367 450 A76 76 0 0 1 519 450"/>
    </defs>
    <rect width="520" height="340" fill="url(#waterTextureB)" role="img" aria-label="Dark background covered in water droplets"/>
    <path d="M0 232 C130 200 250 210 330 290 C400 360 470 380 520 350 L520 735 L0 735 Z" fill="var(--navy)"/>
    <path d="M0 214 C130 182 250 192 330 272 C400 342 470 362 520 332" fill="none" stroke="var(--blue)" stroke-width="16"/>
    <path d="M0 228 C130 196 250 206 330 286 C400 356 470 376 520 346" fill="none" stroke="var(--sky)" stroke-width="6"/>
    <path d="M0 468 L340 468 L322 506 L0 506 Z" fill="var(--sky)"/>
    <rect x="0" y="522" width="128" height="150" fill="#9aa3ad" role="img" aria-label="Photo of gloved hands tightening a pipe fitting with a wrench"/>
    <rect x="131" y="522" width="128" height="150" fill="#3c5a86" role="img" aria-label="Photo of a plumber in blue overalls with a tool belt"/>
    <rect x="262" y="522" width="128" height="150" fill="#c7ccd2" role="img" aria-label="Photo of hands installing a chrome tap"/>
    <rect x="393" y="522" width="127" height="150" fill="#d8c79a" role="img" aria-label="Photo of plumbing fittings and plans on a workbench"/>
    <rect x="0" y="672" width="520" height="63" fill="var(--navy-deep)"/>
    <text font-family="Montserrat, sans-serif" font-size="13" font-weight="600" fill="#fff" letter-spacing="1.5"><textPath href="#badgeArc" startOffset="50%" text-anchor="middle">EMERGENCY SERVICE</textPath></text>
    <circle cx="443" cy="450" r="62" fill="var(--navy)" stroke="#fff" stroke-width="4"/>
    <circle cx="443" cy="450" r="50" fill="var(--red)"/>
  </svg>
  <div class="brand"><span class="brand__dot"></span><span class="brand__name">Kelbrook<br>Plumbing</span></div>
  <h2 class="headline"><span class="headline__lead">Need a Premium</span><span class="headline__main">PLUMBING</span><span class="headline__tail">Service?</span></h2>
  <ul class="ticks ticks--promise">
    <li><svg class="tick" viewBox="0 0 14 14"><circle cx="7" cy="7" r="7" fill="#fff"/><path d="M3.8 7.2l2.2 2.2 4.2-4.4" fill="none" stroke="#0b2a50" stroke-width="1.8"/></svg>We guarantee your satisfaction.</li>
    <li><svg class="tick" viewBox="0 0 14 14"><circle cx="7" cy="7" r="7" fill="#fff"/><path d="M3.8 7.2l2.2 2.2 4.2-4.4" fill="none" stroke="#0b2a50" stroke-width="1.8"/></svg>No job is ever done until you're 100% satisfied.</li>
    <li><svg class="tick" viewBox="0 0 14 14"><circle cx="7" cy="7" r="7" fill="#fff"/><path d="M3.8 7.2l2.2 2.2 4.2-4.4" fill="none" stroke="#0b2a50" stroke-width="1.8"/></svg>We provide upfront pricing.</li>
    <li><svg class="tick" viewBox="0 0 14 14"><circle cx="7" cy="7" r="7" fill="#fff"/><path d="M3.8 7.2l2.2 2.2 4.2-4.4" fill="none" stroke="#0b2a50" stroke-width="1.8"/></svg>We treat your property like our own.</li>
  </ul>
  <p class="badge__time"><span class="badge__hours">24H</span><span class="badge__label">SERVICE</span></p>
  <p class="call">CALL US : 0400 555 218</p>
  <p class="contact">www.kelbrookplumbing.com | info@kelbrookplumbing.com</p>
  <p class="licence"><span class="licence__label">Licence Number</span><span class="licence__number">204817</span></p>
</article>

</body>
</html>
```